Google Form Graphic to suit our Brand and industry

Create a graphic / image for us to put at the top of our client enquiry google form.
The image will be a section of an architectural home with our branding over the top. Preferably translucent.
The image must suit the shape of the google forms image, which is an elongated rectangle
#003d5d - brand colour

Target Market(s)

residential home owners, high end architectural homes

Industry/Entity Type

Residential construction

Colors
0054AA
0677BA
7BADD7
CADEEF
E8F1F8

Requirements
Must have
• our branding and a photo of an architectural home in the background

```html
<!DOCTYPE html>
<html lang="en">
<head>
<meta charset="utf-8">
<title>Norva Builders – Enquiry Form Header</title>
<link rel="stylesheet" href="https://fonts.googleapis.com/css2?family=Montserrat:wght@400&display=swap">
<style>
  :root {
    --brand-navy: #003d5d;
    --panel-navy: #023a58;
    --photo-sky: #6f8fa8;
    --photo-mid: #3f5d74;
    --photo-deep: #1d3447;
    --canvas-bg: #eef2f5;
    --text-light: #ffffff;
  }
  html, body {
    margin: 0;
    padding: 0;
    width: 1200px;
    height: 733px;
    overflow: hidden;
    background: var(--canvas-bg);
  }
  .canvas {
    position: relative;
    width: 1200px;
    height: 733px;
    display: flex;
    align-items: center;
    justify-content: center;
  }
  .form-header {
    display: block;
    width: 1160px;
    height: 289px;
  }
  .brand-name {
    font-family: "Montserrat", sans-serif;
    font-weight: 400;
    fill: var(--text-light);
    font-size: 40px;
  }
</style>
</head>
<body>
  <main class="canvas">
    <svg class="form-header" viewBox="0 0 770 192" xmlns="http://www.w3.org/2000/svg" aria-label="Norva Builders enquiry form header">
      <defs>
        <clipPath id="header-round">
          <rect x="0" y="0" width="770" height="192" rx="7"/>
        </clipPath>
        <linearGradient id="home-photo-tones" x1="0" y1="0" x2="0" y2="1">
          <stop offset="0" stop-color="var(--photo-sky)"/>
          <stop offset="0.45" stop-color="var(--photo-mid)"/>
          <stop offset="1" stop-color="var(--photo-deep)"/>
        </linearGradient>
      </defs>
      <g clip-path="url(#header-round)">
        <rect class="home-photo" x="0" y="0" width="770" height="192" fill="url(#home-photo-tones)"
              role="img" aria-label="Photograph of a modern architectural home facade with tall vertical windows at dusk"/>
        <rect class="translucent-panel" x="357" y="26" width="385" height="130" fill="var(--panel-navy)" opacity="0.78"/>
        <polygon class="brand-panel" points="0,0 345,0 288,96 345,192 0,192" fill="var(--brand-navy)"/>
        <text class="brand-name" x="96" y="111" textLength="178" lengthAdjust="spacing">NORVA</text>
        <text class="brand-name" x="300" y="111" textLength="376" lengthAdjust="spacing">BUILDERS</text>
      </g>
    </svg>
  </main>
</body>
</html>
```